Larkfield Ridge Management

I need a professional website. My current website is larkfieldridgemanagement.com and I hate it. It was created with some AI tool very quickly because I needed a site up and running with no advanced notice. I’m open to all designs .. I trust you, the professionals will deliver the results I’m anxiously awaiting! :)

```html
<!DOCTYPE html>
<html lang="en">
<head>
<meta charset="utf-8">
<title>Larkfield Ridge Management</title>
<link href="https://fonts.googleapis.com/css2?family=Montserrat:wght@600;700&family=Lato:wght@400;700&display=swap" rel="stylesheet">
<style>
:root{
  --navy:#1f355e;
  --navy-deep:#1d3360;
  --red:#d12a2f;
  --ink:#3b3f47;
  --white:#ffffff;
  --line:#8d9bb8;
}
*{margin:0;padding:0;box-sizing:border-box}
html,body{width:1200px;height:3896px;overflow:hidden}
body{position:relative;background:var(--white);font-family:'Lato',sans-serif;color:var(--ink)}
.abs{position:absolute}
.btn{position:absolute;background:var(--red);color:var(--white);border-radius:22px;font:400 15px 'Lato',sans-serif;display:flex;align-items:center;justify-content:center}
.h2{position:absolute;font:700 41px/51px 'Montserrat',sans-serif;color:var(--navy);text-transform:uppercase;letter-spacing:.3px}
.rule{position:absolute;height:3px;background:var(--red)}
.photo{position:absolute;border-radius:30px}

/* hero */
.hero{left:0;top:0;width:1200px;height:754px;background:linear-gradient(90deg,#3a2e28 0%,#4a3a30 25%,#3d4a5c 45%,#46566b 70%,#3a4554 100%)}
.hero-floor{left:0;top:560px;width:1200px;height:194px;background:linear-gradient(180deg,rgba(90,55,35,.0),rgba(80,48,30,.75))}
.brand{left:106px;top:86px;display:flex;align-items:center;gap:10px;font:700 20px 'Montserrat',sans-serif;color:var(--white)}
.brand-dot{width:14px;height:14px;background:var(--white);border-radius:50%}
.nav{top:51px;font:400 15px 'Lato',sans-serif;color:var(--white)}
.nav.active{color:#e2453f}
.nav.active::after{content:"";position:absolute;left:10px;right:10px;top:24px;height:2px;background:#e2453f}
.hero-title{left:463px;top:182px;font:700 48px/65px 'Montserrat',sans-serif;color:var(--white)}
.hero-text{left:467px;top:325px;width:518px;font:400 23px/30px 'Lato',sans-serif;color:var(--white);text-align:justify}

/* solutions */
.solutions{left:0;top:1770px;width:1200px;height:947px;background:var(--navy-deep)}
.sol-title{left:0;width:1200px;top:1870px;text-align:center;font:700 40px/51px 'Montserrat',sans-serif;color:var(--white)}
.sol-text{left:260px;width:680px;top:2015px;text-align:center;font:400 16.5px/27px 'Lato',sans-serif;color:var(--white)}
.card-label{left:227px;width:746px;top:2502px;text-align:center;font:700 31px 'Montserrat',sans-serif;color:var(--white)}
.dot{position:absolute;top:2614px;width:5px;height:5px;border-radius:50%;background:var(--white)}

/* form */
.field{position:absolute;left:720px;width:370px;height:42px;border:1.5px solid var(--line);border-radius:8px;padding:9px 20px;font:400 15px 'Lato',sans-serif;color:var(--ink)}
.body-text{position:absolute;font:400 16.5px/26.5px 'Lato',sans-serif;color:var(--ink);text-align:justify}

/* footer */
.footer{left:0;top:3500px;width:1200px;height:396px;background:var(--navy-deep)}
.f-head{position:absolute;top:3592px;font:700 20px 'Lato',sans-serif;color:var(--white)}
.f-link{position:absolute;font:400 15px 'Lato',sans-serif;color:var(--white)}
.f-rule{left:112px;top:3848px;width:976px;height:1px;background:rgba(255,255,255,.35)}
.copy{left:0;width:1200px;top:3865px;text-align:center;font:400 12.5px 'Lato',sans-serif;color:var(--white)}
</style>
</head>
<body>

<!-- Hero -->
<div class="abs hero" role="img" aria-label="Modern living room with leather sofa, fireplace and armchair"></div>
<div class="abs hero-floor"></div>
<div class="abs brand"><span class="brand-dot"></span>Larkfield Ridge</div>
<a class="abs nav active" style="left:420px">Home</a>
<a class="abs nav" style="left:522px">Services</a>
<a class="abs nav" style="left:637px">About Us</a>
<a class="abs nav" style="left:760px">Contact Us</a>
<div class="btn" style="left:890px;top:39px;width:198px;height:43px">Request a Proposal</div>
<h1 class="abs hero-title">MANAGING PROPERTIES.<br>BUILDING VALUE.</h1>
<p class="abs hero-text">Professional solutions for property owners, delivering dependable service, qualified tenants, and long-term value.</p>
<div class="btn" style="left:463px;top:455px;width:198px;height:41px">Request a Proposal</div>

<!-- Trusted partner -->
<h2 class="h2" style="left:107px;top:877px">Your Trusted<br>Partner in Property<br>Management</h2>
<div class="rule" style="left:107px;top:1039px;width:161px"></div>
<p class="body-text" style="left:726px;top:877px;width:364px;text-align:left">At Larkfield Ridge Management, we're committed to making property ownership simple, profitable, and stress-free.</p>
<div class="btn" style="left:726px;top:994px;width:199px;height:41px">Request a Proposal</div>
<div class="photo" style="left:112px;top:1094px;width:564px;height:526px;background:linear-gradient(135deg,#e7e1d8,#c9b9a3 55%,#8d7a66)" role="img" aria-label="Property manager showing a couple around a bright home"></div>
<div class="photo" style="left:726px;top:1094px;width:362px;height:248px;background:linear-gradient(135deg,#c8c6c0,#a59c8f 60%,#6f6a64)" role="img" aria-label="Modern dining area with pendant lights"></div>
<div class="photo" style="left:726px;top:1369px;width:362px;height:247px;background:linear-gradient(180deg,#d9b7cc 0%,#8a8f99 45%,#4b4f57 75%,#8b8b88 100%)" role="img" aria-label="Two-storey modern house at dusk"></div>

<!-- Solutions -->
<div class="abs solutions"></div>
<h2 class="abs sol-title">STRATEGIC PROPERTY<br>MANAGEMENT SOLUTIONS</h2>
<div class="rule" style="left:519px;top:1987px;width:160px"></div>
<p class="abs sol-text">Our analysis demonstrates that effective property oversight originates from meticulous operational planning, transparent communication channels, and data-driven performance metrics across every asset class.</p>
<div class="photo" style="left:-40px;top:2180px;width:209px;height:368px;background:linear-gradient(135deg,#efe9df,#d9c6ad 60%,#b98a62)" role="img" aria-label="Calla lilies and a small lamp on a table"></div>
<div class="photo" style="left:227px;top:2151px;width:746px;height:426px;background:linear-gradient(135deg,#8a7560 0%,#c9b194 40%,#d8c4a6 65%,#6b5846 100%)" role="img" aria-label="Hands arranging material samples on a wooden table"></div>
<div class="abs card-label">BASIC SERVICE</div>
<div class="photo" style="left:1030px;top:2180px;width:210px;height:368px;background:linear-gradient(135deg,#e5ddd0,#c8b59b 60%,#3a3430)" role="img" aria-label="Globe table lamp on a dark shelf"></div>
<div class="abs" style="left:569px;top:2609px;width:16px;height:16px;border:1.5px solid #fff;border-radius:50%"></div>
<div class="dot" style="left:575px"></div>
<div class="dot" style="left:591px"></div>
<div class="dot" style="left:608px"></div>
<div class="dot" style="left:624px"></div>

<!-- Proposal form -->
<h2 class="h2" style="left:110px;top:2836px">Request a Tailored<br>Proposal</h2>
<div class="rule" style="left:112px;top:2949px;width:161px"></div>
<div class="photo" style="left:113px;top:2997px;width:501px;height:362px;background:linear-gradient(135deg,#6b6258,#b4a590 45%,#d4c6b1 70%,#4a4139)" role="img" aria-label="Minimal bathroom vanity with faucet and round mirror"></div>
<p class="body-text" style="left:726px;top:2840px;width:362px">Submit the form to initiate a consultative assessment and explore solutions aligned with your objectives.</p>
<div class="field" style="top:2964px">First Name</div>
<div class="field" style="top:3020px">Last Name</div>
<div class="field" style="top:3077px">Email</div>
<div class="field" style="top:3133px;height:153px">Message</div>
<div class="btn" style="left:726px;top:3313px;width:165px;height:41px">Send Message</div>

<!-- Footer -->
<div class="abs footer"></div>
<div class="f-head" style="left:112px">Contact Us</div>
<div class="f-head" style="left:508px">Main Links</div>
<div class="f-head" style="left:725px">Services</div>
<div class="f-head" style="left:974px">Other Links</div>

<svg class="abs" style="left:112px;top:3650px" width="20" height="20" viewBox="0 0 24 24" fill="none" stroke="#fff" stroke-width="1.6"><path d="M5 3h4l2 5-2.5 1.5a11 11 0 0 0 6 6L16 13l5 2v4a2 2 0 0 1-2 2A16 16 0 0 1 3 5a2 2 0 0 1 2-2z"/></svg>
<div class="f-link" style="left:151px;top:3652px">+ 1 555 010 0188</div>
<svg class="abs" style="left:112px;top:3696px" width="20" height="18" viewBox="0 0 24 20" fill="none" stroke="#fff" stroke-width="1.6"><rect x="2" y="2" width="20" height="16" rx="2"/><path d="M2 4l10 7 10-7"/></svg>
<div class="f-link" style="left:151px;top:3696px">info@larkfieldridgemanagement.com</div>
<svg class="abs" style="left:113px;top:3742px" width="18" height="22" viewBox="0 0 20 24" fill="none" stroke="#fff" stroke-width="1.6"><path d="M10 22s7-7.5 7-13a7 7 0 0 0-14 0c0 5.5 7 13 7 13z"/></svg>
<div class="f-link" style="left:151px;top:3743px;line-height:26px">123, Larkfield Ridge Management<br>LLC, na 123456.</div>

<div class="f-link" style="left:508px;top:3645px">Home</div>
<div class="f-link" style="left:508px;top:3684px">Services</div>
<div class="f-link" style="left:508px;top:3723px">About Us</div>
<div class="f-link" style="left:508px;top:3761px">Contact Us</div>

<div class="f-link" style="left:725px;top:3645px">Basic Service</div>
<div class="f-link" style="left:725px;top:3684px">Intermediate Service</div>
<div class="f-link" style="left:725px;top:3723px">Advanced Service</div>
<div class="f-link" style="left:725px;top:3761px">Advanced+ Service</div>

<div class="f-link" style="left:974px;top:3652px">Service Areas</div>
<div class="f-link" style="left:974px;top:3691px">Privacy Policy</div>
<div class="f-link" style="left:974px;top:3730px">Terms of Service</div>
<div class="f-link" style="left:974px;top:3768px">Sitemap</div>

<div class="abs f-rule"></div>
<div class="abs copy">Copyright © 2026 Larkfield Ridge Management LLC. All rights reserved.</div>

</body>
</html>
```